Corportate Power Point Template

We need a corporate PPT Design for our startup Big Data company.

Basically, our company will ingest, analyze and generate dynamic Dashboards with data consumed from different sources like Social Networks, Enterprise Legacy Systems such as e-Commerce, ERP, CRM and others.

Company is headquartered in Brazil, but will have a global presence.

Industry/Entity Type

It Company

```html
<!DOCTYPE html>
<html lang="en">
<head>
<meta charset="utf-8">
<title>Project Title Here</title>
<link rel="stylesheet" href="https://fonts.googleapis.com/css2?family=Arimo:wght@400;700&family=Roboto+Condensed:wght@400&display=swap">
<style>
  :root {
    --brand-orange: #f26a1b;
    --ink-dark: #1f1f1f;
    --ink-mid: #3a3a3a;
    --paper: #fffdfb;
    --paper-warm: #fdf0e6;
    --rule-soft: #f1c9a8;
    --line-orange: #ff7800;
    --line-grey: #7b7b7b;
    --line-sand: #ddd7c8;
    --axis: #4a4a4a;
  }
  * { margin: 0; padding: 0; box-sizing: border-box; }
  html, body { width: 1200px; height: 900px; overflow: hidden; }
  body {
    position: relative;
    font-family: "Arimo", Arial, sans-serif;
    background: linear-gradient(160deg, var(--paper-warm) 0%, var(--paper) 35%, var(--paper) 70%, var(--paper-warm) 100%);
  }
  .slide-header {
    position: absolute; left: 0; top: 0; width: 1200px; height: 105px;
    background: linear-gradient(180deg, #ffffff 0%, #fff6ef 70%, #fde9da 100%);
    border-bottom: 2px solid var(--rule-soft);
  }
  .slide-title {
    position: absolute; left: 33px; top: 24px;
    font-size: 52px; font-weight: 700; letter-spacing: -0.5px; line-height: 1.1;
    color: var(--ink-dark);
  }
  .slide-title .accent { color: var(--brand-orange); }
  .chart {
    position: absolute; left: 0; top: 0; width: 1200px; height: 900px;
  }
  .chart text {
    font-family: "Arimo", Arial, sans-serif; font-size: 8.5px; fill: var(--ink-mid);
  }
  .slide-footer {
    position: absolute; left: 0; top: 806px; width: 1200px; height: 94px;
    background: linear-gradient(180deg, #fff3ea 0%, #ffffff 45%);
    border-top: 2px solid var(--rule-soft);
  }
  .brand {
    position: absolute; left: 20px; top: 28px;
    display: flex; align-items: center; gap: 12px;
    font-size: 38px; font-weight: 400; line-height: 1; color: var(--brand-orange);
    letter-spacing: -0.5px;
  }
  .brand-mark { width: 26px; height: 26px; background: var(--brand-orange); }
  .presenter {
    position: absolute; right: 16px; top: 42px;
    font-family: "Roboto Condensed", "Arial Narrow", sans-serif;
    font-size: 18px; color: var(--ink-dark);
  }
  .presenter .name { color: var(--brand-orange); }
</style>
</head>
<body>
  <header class="slide-header">
    <h1 class="slide-title"><span class="accent">Project</span> Title Here</h1>
  </header>

  <svg class="chart" viewBox="0 0 800 600" role="img" aria-label="Line chart with four series rising from 0 to about 13 over six periods">
    <g class="axes" stroke="var(--axis)" stroke-width="1.6" fill="none">
      <path d="M189,150 V456 H645"/>
      <path d="M189,412 h-4 M189,368 h-4 M189,325 h-4 M189,281 h-4 M189,237 h-4 M189,193 h-4 M189,150 h-4"/>
      <path d="M341,456 v6 M493,456 v6"/>
    </g>
    <g class="y-labels" text-anchor="end">
      <text x="175" y="459">0</text>
      <text x="175" y="415">2</text>
      <text x="175" y="371">4</text>
      <text x="175" y="328">6</text>
      <text x="175" y="284">8</text>
      <text x="175" y="240">10</text>
      <text x="175" y="196">12</text>
      <text x="175" y="153">14</text>
    </g>
    <g class="x-labels" text-anchor="middle">
      <text x="261" y="475">2</text>
      <text x="417" y="475">4</text>
      <text x="571" y="475">6</text>
    </g>
    <g class="series" fill="none" stroke-width="3.6" stroke-linecap="round" stroke-linejoin="round">
      <path stroke="var(--line-sand)" d="M189,456 C205,420 225,370 240,373 S260,380 270,365 S295,335 310,340 S335,340 345,325 S365,305 380,305 S420,320 430,310 S445,285 455,283 S490,295 510,285 S540,245 560,240 S580,230 590,215 S630,185 643,175"/>
      <path stroke="var(--line-grey)" d="M189,456 C215,410 230,380 240,380 S275,385 285,372 S310,325 322,323 S370,325 380,315 S390,298 395,295 S440,270 460,268 S495,270 500,260 S525,245 540,240 S570,230 578,225 S625,180 638,168"/>
      <path stroke="var(--line-orange)" d="M189,456 C210,432 238,365 265,357 C300,348 340,345 355,341 C365,338 370,334 378,325 C398,297 415,265 430,262 C460,258 520,255 562,252 C570,251 572,246 573,226 C574,208 577,202 588,195 L636,162"/>
      <path stroke="var(--line-orange)" d="M189,456 C210,445 230,438 250,437 S330,435 345,433 S360,440 375,440 S430,432 465,430 S490,436 515,438 S600,440 640,439"/>
    </g>
  </svg>

  <footer class="slide-footer">
    <div class="brand"><span class="brand-mark"></span>Northvane Data</div>
    <p class="presenter">Presentatator Name : <span class="name">Marina Coutinho</span></p>
  </footer>
</body>
</html>
```